Web Application UI Design

Looking for a light weight UI re-design with complete html files and images for an existing project. As you can see from the uploaded files, the current design is clunky. We are looking to redesign the web application with state of the art light weight UI (Must include bootstrap and should be able to support angular)

Requirements
Must have
• Must have lightweight design preferably with material and bootstrap design
Nice to have
• The screen shots I uploaded show that the design is clunky. I am looking for some new designs

```html
<!DOCTYPE html>
<html lang="en">
<head>
<meta charset="utf-8">
<title>Add New Stackbox Image</title>
<link href="https://fonts.googleapis.com/css2?family=Source+Sans+3:wght@400;600;700&display=swap" rel="stylesheet">
<style>
:root{
  --sidebar-top:#2f3fdc;
  --sidebar-bottom:#1d2cb4;
  --sidebar-sub:#1a27a0;
  --accent:#2433e0;
  --page:#f3f3f5;
  --white:#ffffff;
  --field:#f4f4f6;
  --text:#1f2233;
  --muted:#6f7384;
  --line:#e6e7ec;
}
*{box-sizing:border-box;margin:0;padding:0}
html,body{width:1200px;height:675px;overflow:hidden}
body{font-family:"Source Sans 3",sans-serif;background:var(--page);color:var(--text);position:relative}
.sidebar{position:absolute;left:0;top:0;width:187px;height:675px;background:linear-gradient(180deg,var(--sidebar-top),var(--sidebar-bottom));color:var(--white)}
.brand{position:absolute;left:50px;top:13px;font-size:14px;font-weight:600}
.nav{position:absolute;top:118px;left:0;width:100%;list-style:none}
.nav-item{display:flex;align-items:center;height:36px;padding:0 22px;font-size:13px;gap:10px}
.nav-item svg{width:16px;height:16px;flex:none}
.nav-item .caret{margin-left:auto;width:10px;height:10px}
.subnav{list-style:none;background:var(--sidebar-sub);padding:6px 0}
.subnav li{font-size:12px;height:32px;line-height:32px;padding-left:50px}
.topbar{position:absolute;left:187px;top:0;right:0;height:45px;background:var(--white)}
.search{position:absolute;left:49px;top:6px;width:544px;height:32px;background:var(--field);border-radius:4px;display:flex;align-items:center;padding-left:14px;gap:10px;font-size:12px;color:var(--muted)}
.user{position:absolute;right:36px;top:6px;display:flex;align-items:center;gap:14px;font-size:14px;font-weight:600}
.avatar{width:33px;height:33px;border-radius:50%;background:radial-gradient(circle at 50% 40%,#6a4030,#1e120e)}
.card{position:absolute;left:430px;top:86px;width:452px;height:548px;background:var(--white);border-radius:6px;box-shadow:0 2px 10px rgba(20,25,60,.06)}
.card-title{position:absolute;top:20px;width:100%;text-align:center;font-size:17px;font-weight:600}
.field{position:absolute;left:29px;width:370px;background:var(--field);border-radius:3px;font-size:11px;color:var(--muted);padding:0 10px;display:flex;align-items:center}
.field.area{align-items:flex-start;padding-top:10px}
.field .chev{margin-left:auto;width:8px;height:8px}
.list-label{position:absolute;top:311px;font-size:11px;color:var(--muted)}
.list{position:absolute;top:327px;width:168px;height:135px;background:var(--field)}
.move{position:absolute;left:205px;width:17px;height:17px;border-radius:50%;background:var(--accent);display:flex;align-items:center;justify-content:center}
.move svg{width:7px;height:7px}
.btn{position:absolute;top:494px;width:104px;height:31px;border-radius:4px;font-size:12px;font-weight:600;display:flex;align-items:center;justify-content:center}
.btn-cancel{left:102px;border:1.5px solid var(--accent);color:var(--accent);background:var(--white)}
.btn-build{left:222px;background:var(--accent);color:var(--white)}
</style>
</head>
<body>
<aside class="sidebar">
  <div class="brand">Nimbus</div>
  <ul class="nav">
    <li class="nav-item"><svg viewBox="0 0 16 16" fill="none" stroke="#fff" stroke-width="1.3"><circle cx="8" cy="8" r="2.5"/><circle cx="8" cy="8" r="6"/></svg>Services</li>
    <li class="nav-item"><svg viewBox="0 0 16 16" fill="none" stroke="#fff" stroke-width="1.3"><rect x="2" y="2" width="5" height="5"/><rect x="9" y="2" width="5" height="5"/><rect x="2" y="9" width="5" height="5"/><rect x="9" y="9" width="5" height="5"/></svg>Dashboard<svg class="caret" viewBox="0 0 10 10" fill="none" stroke="#fff" stroke-width="1.3"><path d="M2 3.5l3 3 3-3"/></svg></li>
    <li class="nav-item"><svg viewBox="0 0 16 16" fill="none" stroke="#fff" stroke-width="1.3"><path d="M6.5 9.5l3-3M5 8l-2 2a2.5 2.5 0 003.5 3.5l2-2M11 8l2-2A2.5 2.5 0 009.5 2.5l-2 2"/></svg>Connectors<svg class="caret" viewBox="0 0 10 10" fill="none" stroke="#fff" stroke-width="1.3"><path d="M2 3.5l3 3 3-3"/></svg></li>
    <li class="nav-item"><svg viewBox="0 0 16 16" fill="none" stroke="#fff" stroke-width="1.3"><circle cx="8" cy="4" r="2"/><circle cx="4" cy="12" r="2"/><circle cx="12" cy="12" r="2"/><path d="M8 6v3M6 11l2-2 2 2"/></svg>Ingestion<svg class="caret" viewBox="0 0 10 10" fill="none" stroke="#fff" stroke-width="1.3"><path d="M2 3.5l3 3 3-3"/></svg></li>
    <li class="nav-item"><svg viewBox="0 0 16 16" fill="none" stroke="#fff" stroke-width="1.3"><rect x="2" y="2.5" width="12" height="11"/><path d="M2 6h12M6 6v7.5"/></svg>WorkBench<svg class="caret" viewBox="0 0 10 10" fill="none" stroke="#fff" stroke-width="1.3"><path d="M2 3.5l3 3 3-3"/></svg></li>
    <li class="nav-item"><svg viewBox="0 0 16 16" fill="none" stroke="#fff" stroke-width="1.3"><circle cx="8" cy="5" r="3"/><path d="M2.5 14a5.5 5.5 0 0111 0"/></svg>Administration<svg class="caret" viewBox="0 0 10 10" fill="none" stroke="#fff" stroke-width="1.3"><path d="M2 6.5l3-3 3 3"/></svg></li>
    <li>
      <ul class="subnav">
        <li>Users</li>
        <li>Settings</li>
        <li>Custom Images</li>
      </ul>
    </li>
  </ul>
</aside>

<header class="topbar">
  <div class="search"><svg width="12" height="12" viewBox="0 0 12 12" fill="none" stroke="#6f7384" stroke-width="1.3"><circle cx="5" cy="5" r="3.5"/><path d="M7.7 7.7L11 11"/></svg>Search Anything</div>
  <div class="user">Daniel Harper<div class="avatar" role="img" aria-label="User profile photo"></div></div>
</header>

<main class="card">
  <h1 class="card-title">Add New Stackbox Image</h1>
  <div class="field" style="top:69px;height:32px">Image Name</div>
  <div class="field area" style="top:116px;height:82px">Description</div>
  <div class="field" style="top:214px;height:32px">Kernal<svg class="chev" viewBox="0 0 8 8" fill="#8a8fb0"><path d="M1 2.5h6L4 6z"/></svg></div>
  <div class="field" style="top:262px;height:32px">Base Image<svg class="chev" viewBox="0 0 8 8" fill="#8a8fb0"><path d="M1 2.5h6L4 6z"/></svg></div>

  <span class="list-label" style="left:29px">Available Packages</span>
  <span class="list-label" style="left:231px">Selected Packages</span>
  <div class="list" style="left:29px"></div>
  <div class="list" style="left:231px"></div>

  <div class="move" style="top:351px"><svg viewBox="0 0 8 8" fill="none" stroke="#fff" stroke-width="1.4"><path d="M1 1l3 3-3 3M4 1l3 3-3 3"/></svg></div>
  <div class="move" style="top:374px"><svg viewBox="0 0 8 8" fill="none" stroke="#fff" stroke-width="1.4"><path d="M2.5 1l3 3-3 3"/></svg></div>
  <div class="move" style="top:397px"><svg viewBox="0 0 8 8" fill="none" stroke="#fff" stroke-width="1.4"><path d="M5.5 1l-3 3 3 3"/></svg></div>
  <div class="move" style="top:420px"><svg viewBox="0 0 8 8" fill="none" stroke="#fff" stroke-width="1.4"><path d="M7 1L4 4l3 3M4 1L1 4l3 3"/></svg></div>

  <div class="btn btn-cancel">Cancel</div>
  <div class="btn btn-build">Build Image</div>
</main>
</body>
</html>
```